One business card required with 2 company logos and 2 people's details

One business card required.
No preference on design - One side could show the 2 different business logos for the companies we own. The reverse could have the details shown below.
Another option could be one business one side and one business on the reverse. Happy to receive designs.

Dora Pellham
07700 913 286
Rowena Tindall
07700 958 137

website: quietmeadowbloom.co.uk
email: info@quietmeadowbloom.co.uk

website: brightharbourevents.co.uk
email: info:brightharbourevents.co.uk

May be nice to have icons instead of the words email/website?

I have included different versions of the logos to help with your design.

Contact Information for Business Card

see project overview

Requirements
Must have
• both company logos, both contact names and contact details

```html
<!DOCTYPE html>
<html lang="en">
<head>
<meta charset="utf-8">
<title>Business Card – Quiet Meadow Bloom &amp; Bright Harbour Events</title>
<link href="https://fonts.googleapis.com/css2?family=Montserrat:wght@600&family=Arimo:wght@400&display=swap" rel="stylesheet">
<style>
  :root {
    --stage: #2b2b2d;
    --night-deep: #0c1c27;
    --night-mid: #163442;
    --night-glow: #1f5a66;
    --teal: #3fd3e0;
    --blue: #1a63d3;
    --blue-logo: #1e72e0;
    --paper: #ffffff;
    --ink: #2a2a2a;
    --ring: #49b6e8;
  }
  * { margin: 0; padding: 0; box-sizing: border-box; }
  html, body { width: 1200px; height: 900px; overflow: hidden; }
  body {
    background: var(--stage);
    display: flex; flex-direction: column; align-items: center; justify-content: center;
    gap: 44px;
    font-family: "Arimo", Arial, sans-serif;
  }
  .card {
    position: relative;
    width: 640px; height: 380px;
    border-radius: 4px;
    overflow: hidden;
    box-shadow: 0 14px 30px rgba(0,0,0,.45);
  }

  /* Front */
  .card--front {
    background:
      radial-gradient(ellipse 55% 60% at 50% 48%, var(--night-glow) 0%, rgba(31,90,102,0) 70%),
      linear-gradient(160deg, var(--night-mid), var(--night-deep));
  }
  .front-brand {
    position: absolute; left: 50%; top: 50%;
    transform: translate(-50%, -50%);
    display: flex; flex-direction: column; align-items: center; gap: 18px;
  }
  .front-brand__ring {
    width: 26px; height: 26px; border-radius: 50%;
    border: 2px solid var(--ring);
  }
  .front-brand__name {
    font-family: "Montserrat", sans-serif; font-weight: 600;
    font-size: 30px; letter-spacing: 1px; color: var(--paper);
  }

  /* Back */
  .card--back { background: var(--paper); }
  .back-brand {
    position: absolute; left: 40px; top: 150px;
    display: flex; align-items: center; gap: 12px;
  }
  .back-brand__mark {
    width: 22px; height: 22px; background: var(--blue-logo);
  }
  .back-brand__name {
    font-family: "Montserrat", sans-serif; font-weight: 600;
    font-size: 26px; color: var(--blue-logo); line-height: 1.15;
  }
  .people {
    position: absolute; right: 0; top: 32px;
    display: flex; flex-direction: column; align-items: flex-end; gap: 14px;
  }
  .person { display: flex; flex-direction: column; align-items: flex-end; }
  .person__name {
    background: linear-gradient(90deg, var(--teal), var(--blue));
    color: var(--paper);
    font-family: "Montserrat", sans-serif; font-weight: 600;
    font-size: 22px;
    padding: 7px 26px 7px 30px;
  }
  .person__phone {
    display: flex; align-items: center; gap: 14px;
    font-size: 15px; color: var(--ink);
    margin: 7px 22px 0 0;
  }
  .icon { width: 16px; height: 16px; flex: none; }
  .contacts {
    position: absolute; right: 22px; bottom: 44px;
    list-style: none;
    display: flex; flex-direction: column; align-items: flex-end; gap: 4px;
  }
  .contacts li {
    display: flex; align-items: center; gap: 14px;
    font-size: 15px; color: var(--ink);
  }
  .back-stripe {
    position: absolute; left: 0; right: 0; bottom: 0; height: 12px;
    background: linear-gradient(90deg, var(--blue), var(--teal) 55%, var(--blue));
  }
</style>
</head>
<body>

  <section class="card card--front" aria-label="Card front">
    <div class="front-brand">
      <span class="front-brand__ring"></span>
      <span class="front-brand__name">Quiet Meadow Bloom</span>
    </div>
  </section>

  <section class="card card--back" aria-label="Card back">
    <div class="back-brand">
      <span class="back-brand__mark"></span>
      <span class="back-brand__name">Bright Harbour<br>Events</span>
    </div>

    <div class="people">
      <div class="person">
        <span class="person__name">Dora Pellham</span>
        <span class="person__phone">07700 913 286
          <svg class="icon" viewBox="0 0 16 16" aria-hidden="true"><path fill="#1a63d3" d="M3.2 1.5l2.2 2.6-1.3 1.6c.9 2 2.4 3.5 4.4 4.4l1.6-1.3 2.6 2.2-1.2 2.2C7 13 3 9 1 4.1z"/></svg>
        </span>
      </div>
      <div class="person">
        <span class="person__name">Rowena Tindall</span>
        <span class="person__phone">07700 958 137
          <svg class="icon" viewBox="0 0 16 16" aria-hidden="true"><path fill="#1a63d3" d="M3.2 1.5l2.2 2.6-1.3 1.6c.9 2 2.4 3.5 4.4 4.4l1.6-1.3 2.6 2.2-1.2 2.2C7 13 3 9 1 4.1z"/></svg>
        </span>
      </div>
    </div>

    <ul class="contacts">
      <li>info@brightharbourevents.co.uk
        <svg class="icon" viewBox="0 0 16 16" aria-hidden="true"><rect x="1" y="3" width="14" height="10" fill="#1a63d3"/><path d="M1 3l7 6 7-6" fill="none" stroke="#fff" stroke-width="1.4"/></svg></li>
      <li>www.brightharbourevents.co.uk
        <svg class="icon" viewBox="0 0 16 16" aria-hidden="true"><g fill="none" stroke="#1a63d3" stroke-width="1.3"><circle cx="8" cy="8" r="6.5"/><ellipse cx="8" cy="8" rx="3" ry="6.5"/><path d="M1.5 8h13M2.5 4.8h11M2.5 11.2h11"/></g></svg></li>
      <li>info@quietmeadowbloom.co.uk
        <svg class="icon" viewBox="0 0 16 16" aria-hidden="true"><rect x="1" y="3" width="14" height="10" fill="#1a63d3"/><path d="M1 3l7 6 7-6" fill="none" stroke="#fff" stroke-width="1.4"/></svg></li>
      <li>www.quietmeadowbloom.co.uk
        <svg class="icon" viewBox="0 0 16 16" aria-hidden="true"><g fill="none" stroke="#1a63d3" stroke-width="1.3"><circle cx="8" cy="8" r="6.5"/><ellipse cx="8" cy="8" rx="3" ry="6.5"/><path d="M1.5 8h13M2.5 4.8h11M2.5 11.2h11"/></g></svg></li>
    </ul>

    <div class="back-stripe"></div>
  </section>

</body>
</html>
```